Flyer, poster, banner and social media titles designs for Community Mending Chartre

The Harbourline Charter for Community Mending provide a nationally agreed framework to guide recovery policy and practice across Australia. The Principles support recovery practitioners, governments, non-government organisations and communities to deliver effective, community-centred recovery outcomes.
The Principles have recently been refreshed through extensive consultation and we require a contemporary visual identity and design suite that will increase awareness, engagement and practical application of the Principles.
The redesign will cover:
• A4 Brochure (primary publication)
• A3 Poster
• Pull up banner
• Social Media Tiles
The new design should:
• Create a recognisable brand for the Harbourline Charter.
• Appeal to both experienced and emerging recovery practitioners.
• Reflect contemporary disaster recovery practice.
• Feel people-focused rather than government-focused.
• Support future resources such as videos, implementation guides, presentations and workshop materials.
• Remain relevant for several years without requiring a major redesign.
Target Audience
• Disaster recovery practitioners
• Government agencies
• Non-government organisations
• Community recovery workers
• Recovery managers and leaders
• Community stakeholders and volunteers
The visual identity should reflect the six Principles:
• Understanding Context
• Recognising Complexity
• Community-Centred Approaches
• Coordination
• Communication
• Capacity Building
The design should communicate:
• Recovery is centred on people and communities.
• Recovery is collaborative and involves many sectors.
• Recovery is adaptive, inclusive and evidence-informed.
• Recovery supports resilience and long-term wellbeing.
• The Principles provide practical guidance for recovery practice.
We are looking for:
• Modern and professional
• Warm and approachable
• Human-centred
• Inclusive and accessible
• Australian in context
• Visually engaging
• Suitable for print and digital use
We would like to avoid:
• Images of disaster destruction
• Emergency response imagery (fire trucks, flashing lights, etc.)
• Overly corporate or bureaucratic designs
• Designs that focus on deficits rather than recovery and growth
Consider themes such as:
• Connection and collaboration
• Communities and people
• Growth, recovery and renewal
Accessibility
Designs should:
• Meet accessibility best practice
• Use clear typography
• Achieve strong colour contrast
• Be suitable for both digital and print formats

Deliverables
1. Principles Brochure
• A4 trifold size x 2 (online and print friendly version)
• A side to include cover side, logos side and overview of principles.
• B side full details of the principles
• Graphic to highlight the 3 c’s concept (RECOVERY Context, complexity, community centred, coordinate, communicate and capacity). Currently 3 circles.
• Can be printed and distributed electronically
2. Poster
• A1 and A3 versions
• Suitable for office and workshop display
3. Pull-Up Banner - 850 mm (W) × 2000 mm (H)
• Conference and event use
• High visual impact
• Strong branding and concise messaging
4. Social Media Tiles x 3

We are providing an extension and increasing the budget following feedback from designers. We are wanting the resources to look and feel different from the existing designs, considering either a different colour palette in the designs or different motif with the leave design. Any nature based designs should consider the Australian fauna or flora. Also suggest avoiding images in the designs. The principles are not numbered or liner in the concept of how they function. Happy to answer any further questions and thank you for your suggested concepts.

Disaster recovery practitioners, Government agencies , Non-government organisations, Community recovery workers and Community stakeholders and volunteers

Disaster recovery

• Modern, warm, visually engaging, human-centred, Australian in context and different to the current design.
• Symbols for each principles
• Images of disaster destruction, Emergency response imagery, Overly corporate or bureaucratic designs, Designs that focus on deficits rather than recovery and growth, avoid too much black

```html
<!DOCTYPE html>
<html lang="en">
<head>
<meta charset="utf-8">
<title>Harbourline Charter for Community Mending – Trifold Brochure</title>
<link rel="stylesheet" href="https://fonts.googleapis.com/css2?family=Lato:wght@400;700&family=Lora:wght@400;500&display=swap">
<style>
:root{
  --stage:#7f7f7f;
  --paper:#fbf9f4;
  --paper-warm:#f4ede3;
  --forest:#0e4535;
  --heading-green:#1f4d3e;
  --ink:#2e2e2e;
  --leaf:#6f9a3a;
  --gold:#e0b14a;
  --cream:#f3efe6;
  --context:#4a8a6a;
  --complexity:#6a9040;
  --community:#d9662e;
  --coordinate:#3c6e8a;
  --communicate:#e2a02b;
  --capacity:#d2602a;
}
*{box-sizing:border-box;margin:0;padding:0}
html,body{width:764px;height:1200px;overflow:hidden;background:var(--stage)}
.canvas{position:relative;width:764px;height:1200px;background:var(--stage);font-family:"Lato",sans-serif;color:var(--ink)}
.sheet{position:absolute;left:16.5px;width:727px;height:562px;display:flex}
.sheet-outside{top:25px}
.sheet-inside{top:595px}
.panel{position:relative;height:100%;overflow:hidden}
.panel-left{width:241px;background:var(--paper)}
.panel-middle{width:245.5px;background:var(--paper-warm)}
.panel-right{width:240.5px;background:var(--paper)}
.panel-cover{width:240.5px;background:var(--forest)}

/* overview panel */
.overview-title{position:absolute;left:16px;top:22px;font-family:"Lora",serif;font-weight:400;font-size:16.5px;line-height:21px;color:var(--heading-green)}
.overview-copy{position:absolute;left:16px;top:73px;width:212px;font-size:8.1px;line-height:12.9px;color:#333}
.overview-copy p{margin-bottom:6.5px}
.overview-copy p.gap{margin-top:12px}
.success-title{position:absolute;left:16px;top:428px;font-family:"Lora",serif;font-size:16.5px;line-height:22px;color:var(--heading-green)}
.principle-wheel{position:absolute;left:0;top:0;width:241px;height:562px}
.wheel-label{font-family:"Lato",sans-serif;font-size:5.4px;fill:#2e2e2e;text-anchor:middle}

/* decoration placeholders */
.deco{position:absolute;border-radius:50%}
.deco-sprig{left:20px;top:8px;width:170px;height:100px;background:radial-gradient(ellipse at center,rgba(94,122,96,.55),rgba(94,122,96,0) 70%)}
.deco-cover-leaf{left:138px;top:78px;width:82px;height:56px;background:radial-gradient(ellipse at center,rgba(111,154,58,.75),rgba(111,154,58,0) 70%)}
.deco-cover-fern{left:2px;top:345px;width:236px;height:215px;background:radial-gradient(ellipse at 60% 55%,rgba(205,170,96,.32),rgba(205,170,96,0) 70%)}
.deco-left-leaves{left:-6px;top:480px;width:100px;height:90px;background:radial-gradient(ellipse at center,rgba(90,115,90,.45),rgba(90,115,90,0) 70%)}
.deco-corner{right:-10px;top:-10px;width:70px;height:60px;background:radial-gradient(ellipse at center,rgba(110,135,105,.35),rgba(110,135,105,0) 70%)}
.deco-context-sprig{left:175px;top:240px;width:60px;height:40px;background:radial-gradient(ellipse at center,rgba(110,150,90,.45),rgba(110,150,90,0) 70%)}

/* partner card */
.partner-card{position:absolute;left:18px;top:113px;width:209px;height:416px;background:#fff;border-radius:10px;display:grid;grid-template-columns:1fr 1fr;grid-template-rows:repeat(6,1fr);padding:10px 6px}
.partner{display:flex;flex-direction:column;align-items:center;justify-content:center;gap:4px;text-align:center;font-family:"Lato",sans-serif;font-weight:700;font-size:7.2px;line-height:9px;color:#2b3b35}
.partner-mark{width:20px;height:20px;border-radius:50%;background:#d8ddd9}

/* cover */
.cover-kicker{position:absolute;left:18px;top:52px;font-size:9px;letter-spacing:.3px;color:var(--cream)}
.cover-word{position:absolute;left:17px;font-family:"Lato",sans-serif;font-weight:700;line-height:1}
.cover-word-top{top:64px;font-size:27px;color:#fff}
.cover-word-bottom{top:93px;font-size:25px;color:var(--leaf);font-weight:400}
.cover-title{position:absolute;left:17px;top:158px;width:215px;font-family:"Lora",serif;font-size:31px;line-height:35px;color:var(--cream)}
.cover-tagline{position:absolute;left:18px;top:325px;width:215px;font-family:"Lora",serif;font-size:13.5px;line-height:19px;color:var(--gold)}

/* principles */
.principle{position:absolute;left:16.5px;right:14px}
.principle-head{display:flex;align-items:center;height:34px;gap:8px;margin-bottom:13px}
.principle-icon{flex:none;width:34px;height:34px;border-radius:50%;display:flex;align-items:center;justify-content:center}
.principle-name{font-family:"Lora",serif;font-size:10.5px;line-height:1.1}
.principle-name strong{font-weight:400;font-size:14.5px;letter-spacing:.2px}
.principle-intro{font-size:6.3px;line-height:9.2px;margin-bottom:8px;color:#333}
.principle-points{list-style:none}
.principle-points li{position:relative;padding-left:8.5px;font-size:6.3px;line-height:9.2px;margin-bottom:6px;color:#333}
.principle-points li::before{content:"";position:absolute;left:0;top:2.6px;width:3.6px;height:3.6px;border-radius:50%;background:var(--dot)}
.principle-points.tight li{margin-bottom:4.8px}

.is-context{--dot:var(--context)} .is-context .principle-icon{background:var(--context)} .is-context .principle-name{color:var(--context)}
.is-complexity{--dot:var(--complexity)} .is-complexity .principle-icon{background:var(--complexity)} .is-complexity .principle-name{color:var(--complexity)}
.is-community{--dot:var(--community)} .is-community .principle-icon{background:var(--community)} .is-community .principle-name{color:var(--community)}
.is-coordinate{--dot:var(--coordinate)} .is-coordinate .principle-icon{background:var(--coordinate)} .is-coordinate .principle-name{color:var(--coordinate)}
.is-communicate{--dot:var(--communicate)} .is-communicate .principle-icon{background:var(--communicate)} .is-communicate .principle-name{color:var(--communicate)}
.is-capacity{--dot:var(--capacity)} .is-capacity .principle-icon{background:var(--capacity)} .is-capacity .principle-name{color:var(--capacity)}
</style>
</head>
<body>
<div class="canvas">

  <!-- Outside: overview, partners, cover -->
  <section class="sheet sheet-outside">
    <div class="panel panel-left">
      <div class="deco deco-left-leaves" role="img" aria-label="Soft watercolour eucalyptus leaves"></div>
      <h1 class="overview-title">Harbourline Charter of<br>Community Mending</h1>
      <div class="overview-copy">
        <p>Disasters can deeply impact lives and livelihoods. Working with communities recovering from disasters is complex and challenging. Recovery is long-term, non-linear and dynamic, particularly in the context of compounding and concurrent disasters. These principles are a way to guide our efforts, our approach, our planning and our decision-making.</p>
        <p>Disaster recovery is part of emergency management, which includes the broader components of prevention, preparedness and response. Planning for recovery is integral to emergency preparation, and mitigation actions are often initiated as part of recovery.</p>
        <p class="gap">Disaster recovery includes built, environmental and economic elements, as well as individual and social wellbeing. Recovery can provide an opportunity to improve these aspects beyond previous conditions, by enhancing social and natural environments,</p>
        <p>The relationship between the principles<br>While all the principles are equally critical to ensure effective recovery, understanding the local and broader context and recognising complexity are foundational. The descriptions beneath each principle provide further guidance for working with communities in disaster recovery.</p>
      </div>
      <h2 class="success-title">Successful<br>Recovery</h2>
      <svg class="principle-wheel" viewBox="0 0 241 562" aria-label="Six linked principles around communicating effectively">
        <g fill="none" stroke-width="1.6">
          <circle cx="155.5" cy="442" r="28" stroke="#2f4f3e"/>
          <circle cx="197" cy="469" r="28" stroke="#d9a33a"/>
          <circle cx="111" cy="467" r="28" stroke="#b5a466"/>
          <circle cx="132.5" cy="520" r="28" stroke="#a7442f"/>
          <circle cx="186" cy="517.5" r="28" stroke="#d48a6e"/>
        </g>
        <circle cx="157" cy="482.5" r="29" fill="#fbf9f4" stroke="#c0503a" stroke-width="4"/>
        <circle cx="157" cy="482.5" r="24.5" fill="none" stroke="#e3a190" stroke-width="1"/>
        <text class="wheel-label" x="155.5" y="438">Understand the</text>
        <text class="wheel-label" x="155.5" y="445.5">CONTEXT</text>
        <text class="wheel-label" x="204" y="464">Recognise</text>
        <text class="wheel-label" x="204" y="471.5">COMPLEXITY</text>
        <text class="wheel-label" x="111" y="460">Recognise</text>
        <text class="wheel-label" x="111" y="467.5">and build</text>
        <text class="wheel-label" x="111" y="475">CAPACITY</text>
        <text class="wheel-label" x="157" y="481">COMMUNICATE</text>
        <text class="wheel-label" x="157" y="488.5">effectively</text>
        <text class="wheel-label" x="131" y="522">COORDINATE</text>
        <text class="wheel-label" x="131" y="529.5">all activities</text>
        <text class="wheel-label" x="186" y="510">Use</text>
        <text class="wheel-label" x="186" y="517.5">COMMUNITY-</text>
        <text class="wheel-label" x="186" y="525">CENTRED</text>
        <text class="wheel-label" x="186" y="532.5">approaches</text>
      </svg>
    </div>

    <div class="panel panel-middle">
      <div class="deco deco-sprig" role="img" aria-label="Watercolour sprig of eucalyptus leaves"></div>
      <div class="partner-card" aria-label="Partner organisations">
        <div class="partner"><span class="partner-mark"></span>Federal Office of<br>Community Services</div>
        <div class="partner"><span class="partner-mark"></span>Federal Office of<br>Civic Affairs</div>
        <div class="partner"><span class="partner-mark"></span>Harbour Aid Society</div>
        <div class="partner"><span class="partner-mark"></span>Southgate State Office</div>
        <div class="partner"><span class="partner-mark"></span>Westreach State Office</div>
        <div class="partner"><span class="partner-mark"></span>Islay State Office</div>
        <div class="partner"><span class="partner-mark"></span>Sunreach State Office</div>
        <div class="partner"><span class="partner-mark"></span>Capital Ward Office</div>
        <div class="partner"><span class="partner-mark"></span>Top End Ward Office</div>
        <div class="partner"><span class="partner-mark"></span>Bayside State Office</div>
        <div class="partner"><span class="partner-mark"></span>Coastline Office<br>of Readiness</div>
      </div>
    </div>

    <div class="panel panel-cover">
      <p class="cover-kicker">HARBOURLINE CHARTER FOR</p>
      <p class="cover-word cover-word-top">Community</p>
      <p class="cover-word cover-word-bottom">Mending</p>
      <div class="deco deco-cover-leaf" role="img" aria-label="Green gum leaf sprig"></div>
      <h2 class="cover-title">Harbourline Charter for Community Mending</h2>
      <p class="cover-tagline">Guiding recovery. Strengthening communities.</p>
      <div class="deco deco-cover-fern" role="img" aria-label="Gold line drawing of a leafy branch"></div>
    </div>
  </section>

  <!-- Inside: the six principles -->
  <section class="sheet sheet-inside">
    <div class="panel panel-left">
      <div class="deco deco-context-sprig" role="img" aria-label="Small sprig of green leaves"></div>
      <article class="principle is-context" style="top:9px">
        <header class="principle-head">
          <span class="principle-icon"><svg width="16" height="16" viewBox="0 0 16 16" fill="none" stroke="#fff" stroke-width="1.2"><circle cx="8" cy="6" r="4"/><path d="M6 11h4M6.5 13h3"/></svg></span>
          <h3 class="principle-name">Understand the <strong>CONTEXT:</strong></h3>
        </header>
        <p class="principle-intro">Successful recovery is based on an understanding of the community context, with each community having its own history, values and dynamics. Recovery should:</p>
        <ul class="principle-points">
          <li>Acknowledge existing strengths and capacity, including past experiences and future aspirations;</li>
          <li>Appreciate the risks and stressors faced by the community;</li>
          <li>Embed accessibility, equity, inclusion and diversity in recovery practice, using culturally safe and trauma-informed approaches;</li>
          <li>Support people who may be at greater risk or disproportionately impacted;</li>
          <li>Respect and support connections to Country, environment, animals and culturally significant places and recognise environmental regeneration in recovery;</li>
          <li>Recognise pathways and timeframes vary; systems should support long-term recovery shaped by community needs; and</li>
          <li>Acknowledge the impact upon the community may extend beyond the geographical boundaries where the disaster occurred.</li>
        </ul>
      </article>
      <article class="principle is-complexity" style="top:269px">
        <header class="principle-head">
          <span class="principle-icon"><svg width="16" height="16" viewBox="0 0 16 16" fill="none" stroke="#fff" stroke-width="1.2"><circle cx="7" cy="7" r="4.5"/><path d="M10.5 10.5L14 14"/></svg></span>
          <h3 class="principle-name">Recognise <strong>COMPLEXITY</strong></h3>
        </header>
        <p class="principle-intro">Successful recovery is responsive to the complex and evolving nature of disasters and their impacts on communities, including compounding, cascading and concurrent events. Recovery should recognise that:</p>
        <ul class="principle-points">
          <li>Disasters lead to a range of effects and impacts that require a variety of approaches; they can also leave long-term legacies;</li>
          <li>Information on impacts and needs can be limited at first and changes over time;</li>
          <li>Affected individuals and the community have diverse needs, wants and expectations, which can evolve rapidly;</li>
          <li>Responsive and flexible action is crucial to addressing immediate needs;</li>
          <li>Existing community knowledge and values may challenge the assumptions of those outside of the community;</li>
          <li>Conflicting knowledge, values and priorities among individuals, the community and organisations may create tensions;</li>
          <li>Emergencies create stressful environments where grief or blame may also affect those involved; and</li>
          <li>Over time, appropriate support for individuals and communities, from within and outside, can cultivate hope and individual and collective growth.</li>
        </ul>
      </article>
    </div>

    <div class="panel panel-middle">
      <article class="principle is-community" style="top:9px">
        <header class="principle-head">
          <span class="principle-icon"><svg width="16" height="16" viewBox="0 0 16 16" fill="none" stroke="#fff" stroke-width="1.2"><circle cx="4.5" cy="5" r="1.8"/><circle cx="8" cy="4" r="1.8"/><circle cx="11.5" cy="5" r="1.8"/><path d="M2.5 13v-3a2 2 0 0 1 4 0M6 13V9a2 2 0 0 1 4 0v4M9.5 13v-3a2 2 0 0 1 4 0v3"/></svg></span>
          <h3 class="principle-name">Use <strong>COMMUNITY - LED</strong><br>approaches</h3>
        </header>
        <p class="principle-intro">Successful recovery is community-centred, responsive and flexible, engaging with community and supporting them to move forward, with shared responsibilities. Recovery should:</p>
        <ul class="principle-points">
          <li>Assist and enable individuals, families and the community to actively participate in their own recovery;</li>
          <li>Recognise that individuals and the community may need different levels of support at various times;</li>
          <li>Be guided by the communities' priorities;</li>
          <li>Channel effort through pre-identified and existing community assets, including local knowledge, existing community strengths and resilience;</li>
          <li>Build collaborative partnerships that reflect diverse representation and community leadership in recovery;</li>
          <li>Support Aboriginal and Torres Strait Islander self-determination and Indigenous governance, recognising Country as central to recovery and resilience;</li>
          <li>Recognise that new community leaders often emerge during and after a disaster, who may not hold formal positions of authority; and</li>
          <li>Recognise that different communities may choose different paths to recovery.</li>
        </ul>
      </article>
      <article class="principle is-coordinate" style="top:276px">
        <header class="principle-head">
          <span class="principle-icon"><svg width="16" height="16" viewBox="0 0 16 16" fill="none" stroke="#fff" stroke-width="1.2"><circle cx="8" cy="8" r="5.5"/><circle cx="8" cy="8" r="2"/></svg></span>
          <h3 class="principle-name"><strong>COORDINATE</strong> all activities</h3>
        </header>
        <p class="principle-intro">Successful recovery requires a planned, coordinated and adaptive approach, between community and partner agencies, based on continuing assessment of impacts and need. Recovery should:</p>
        <ul class="principle-points tight">
          <li>Have clearly articulated and shared goals based on desired outcomes;</li>
          <li>Be flexible, taking into account changes in community needs or stakeholder expectations.</li>
          <li>Be guided by those with experience and expertise, using skilled, authentic and capable community leadership;</li>
          <li>Be at the pace desired by the community, and seek to collaborate and reconcile different interests and time frames;</li>
          <li>Reflect well-developed community planning and information gathering before, during and after a disaster;</li>
          <li>Have clear decision-making and reporting structures and sound governance, which are transparent and accessible to the community;</li>
          <li>Demonstrate an understanding of the roles, responsibilities and authority of organisations involved and coordinate across agencies to ensure minimal service provision disruption;</li>
          <li>Be part of an emergency management approach that integrates with response operations and contributes to future prevention and preparedness; and</li>
        </ul>
      </article>
    </div>

    <div class="panel panel-right">
      <div class="deco deco-corner" role="img" aria-label="Faint green leaves in the corner"></div>
      <article class="principle is-communicate" style="top:9px">
        <header class="principle-head">
          <span class="principle-icon"><svg width="16" height="16" viewBox="0 0 16 16" fill="none" stroke="#fff" stroke-width="1.2"><rect x="2" y="2.5" width="12" height="8" rx="1.5"/><path d="M5 10.5L4.5 14l3.5-3.5"/></svg></span>
          <h3 class="principle-name"><strong>COMMUNICATE</strong> effectively</h3>
        </header>
        <p class="principle-intro">Successful recovery is built on effective communication between the affected community and other partners. Recovery should:</p>
        <ul class="principle-points">
          <li>Recognise that communication should be two-way, transparent and ongoing, building trust through shared understanding and feedback;</li>
          <li>Ensure that information is accessible to audiences in diverse situations, addresses a variety of communication needs, and is provided through a range of communication channels and networks;</li>
          <li>Establish mechanisms for coordinated and consistent communications between all service providers, organisations and individuals and the community;</li>
          <li>Ensure that all communication is relevant, timely, clear, accurate, targeted, credible and consistent; and</li>
          <li>Identify trusted sources of information and repeat key recovery messages to enable greater community confidence and receptivity.</li>
        </ul>
      </article>
      <article class="principle is-capacity" style="top:224px">
        <header class="principle-head">
          <span class="principle-icon"><svg width="16" height="16" viewBox="0 0 16 16" fill="none" stroke="#fff" stroke-width="1.2"><circle cx="6" cy="5" r="2.2"/><path d="M2 13a4 4 0 0 1 8 0"/><path d="M12 3v5M9.5 5.5h5"/></svg></span>
          <h3 class="principle-name">Recognise and build <strong>CAPACITY</strong></h3>
        </header>
        <p class="principle-intro">Successful recovery recognises, supports and builds on individual, community and organisational capacity and resilience. Recovery should:</p>
        <ul class="principle-points tight">
          <li>Assess capability and capacity requirements before, during and after a disaster;</li>
          <li>Support the development of self-reliance, preparation and disaster mitigation;</li>
          <li>Quickly identify and mobilise community skills, strengths &amp; resources;</li>
          <li>Develop networks and partnerships to strengthen capacity, capability and resilience;</li>
          <li>Support training and knowledge sharing to sustain recovery capability across staff, volunteers, and the community;</li>
          <li>Ensure mental health and wellbeing supports are available for staff, volunteers and communities involved in disaster recovery;</li>
          <li>Recognise that resources can be provided by a range of partners and from community networks;</li>
          <li>Acknowledge that existing resources may be stretched, and that additional resources may be required;</li>
          <li>Understand that additional resources may only be available for a limited period, and that sustainability may need to be addressed;</li>
          <li>Understand when and how to step back, while continuing to support individuals and the community as a whole to be more self-sufficient when they are ready; and</li>
          <li>Monitor, evaluate and capture learning to strengthen future recovery and preparedness, and build resilience.</li>
        </ul>
      </article>
    </div>
  </section>

</div>
</body>
</html>
```